Start-Up für Training, Coaching & Consulting sucht modernes Webdesign!
Zielgruppe
Wer ist TAVI Training, Coaching & Consulting?
Wir führen Führungskräftetrainings durch, machen Privatkunden für Bewerbungen fit und unterstützen Unternehmen mit Verkaufstrainings. Wir entwickeln Persönlichkeiten im Coaching. Wir beraten Unternehmen und helfen ihnen dabei, ihre Geschäftsabläufe und Prozesse zu optimieren. Dabei steht unsere hohe Qualität im Mittelpunkt - gemeinsam mit unseren kreativen Trainingsmethoden. Unser Background (Diplom-Kaufleute und geprüfte Trainer) bietet dafür die passende Ausgangslage.
Was bedeutet TAVI?
Tavi ist Maori und bdeutet Kreis/Spirale. Er symbolisiert einen wachsenden Silberfarn und steht für persönliche Entwicklung und Entfaltung. Der Tavi ist einerseits unser Namensgeber und unser Logo, andererseits steht der Tavi aber auch für unsere Werte: Denn wir wollen unseren Kunden dabei helfen zu wachsen und sich weiterzuentwickeln - und dies auf eine hochqualitative und seriöse Art und Weise ohne den Eindruck von Esoterik oder Erlebnispädagogik zu vermitteln.
Aufgabenstellung
Modernes Design, das unsere Philosophie widerspiegelt: Wir möchten unseren Kunden auf seriöse und hochqualitative Weise weiterentwickeln. Wir stehen für nachhaltigen Lernerfolg, kreative Trainingsmethoden, Abwechslung, Spaß am Lernen, Qualität, Kompetenz, Fachwissen und Dynamik.
Layout:
1) Header: QMSR geprüfter Trainer, Menüpunkte (siehe Architektur)
2) Banner
3) 3 Teaser (Training, Coaching, Consulting) + Header + 2-3 Zeilen Text (+Icons)
>>> Sichtbarer Bereich auf Homepage: Menü, Banner, Teaser
4) "Warum Sie uns wählen sollten": 5 bullet points ohne weiteren Text
5) "Aus unserem Blog": Frame für 3 Blogartikel + Bild + Datum + Header + 2-3 Zeilen Text
6) Alle drei QMSR Logos
7) Footer: Click Us (quick links), Contact Us (Adresse), Follow Us (Pinnwald, ZOLP, Kontaktor)
8) Copyright + Impressum
>>> Das Design soll klar sein, aber nicht zu kantig. Vielmehr sollen abgerundete Ecken und dynamische Elemente genutzt werden.
Architektur:
3 Ebenen:
1) Homepage
2) TAVI, Training, Coaching, Consulting, für Trainer, Kundenstimmen/Referenzen, Kontakt
3) noch zu bestimmende Produktdetailseiten
Texte werden noch erstellt, Layout kann ggf. mit Platzhaltertext gefüllt werden.
Bildmaterial: Logo und vorhandenes Imagebild werden zur Verfügung gestellt. Bilder können ggf. gekauft werden. Vorschläge erwünscht.
Corporate colors:
grün: #a2c61b + monochromatic colors
http://www.tintoskop.de/a2c61b
grau: #474747 + monochromatic colors
http://www.tintoskop.de/474747

```html
<!DOCTYPE html>
<html lang="de">
<head>
<meta charset="utf-8">
<title>TAVI Training, Coaching &amp; Consulting</title>
<link href="https://fonts.googleapis.com/css2?family=Mulish:wght@300;400;600;700;800&display=swap" rel="stylesheet">
<style>
:root{
  --green:#a2c61b;
  --green-dark:#8fb012;
  --green-pale:#e4edcb;
  --grey:#474747;
  --charcoal:#2a2c2f;
  --night:#232528;
  --text:#5a5a5a;
  --light:#d8d8d8;
  --white:#ffffff;
}
*{margin:0;padding:0;box-sizing:border-box}
html,body{width:750px;height:1200px;overflow:hidden;background:var(--white)}
body{font-family:"Mulish",sans-serif;color:var(--text);position:relative}
.abs{position:absolute}

/* header */
.site-header{left:0;top:0;width:750px;height:50px;background:var(--charcoal)}
.brand{left:118px;top:10px;display:flex;flex-direction:column;align-items:center}
.brand-name{font-size:24px;font-weight:800;color:var(--white);letter-spacing:1px;line-height:24px}
.brand-tag{font-size:4.5px;color:var(--light);margin-top:2px;letter-spacing:.2px}
.main-nav{left:341px;top:0;height:50px;display:flex;align-items:center;font-size:8px;font-weight:600;color:var(--white)}
.main-nav .item{height:50px;display:flex;align-items:center;padding:0 9px}
.main-nav .item.active{color:var(--green);background:#25272a;border-bottom:2px solid var(--green)}
.main-nav .sep{padding:0 4px}
.caret{color:var(--green);margin-left:4px;font-size:7px}

/* hero */
.hero{left:0;top:50px;width:750px;height:230px;background:radial-gradient(ellipse at 45% 70%,#8bb54a 0%,#5f8f2e 45%,#3e6e22 100%)}
.hero-arrow{top:142px}
.hero-title{left:107px;top:112px;color:var(--white);font-size:24px;font-weight:300;line-height:29px;letter-spacing:.3px}
.hero-title b{font-weight:800}
.hero-title .chev{position:absolute;left:-14px;top:0;color:var(--green);font-weight:700}
.hero-sub{left:107px;top:170px;color:var(--white);font-size:11px;line-height:16px;font-weight:400}
.btn{left:105px;top:213px;width:95px;height:31px;border-radius:9px;background:var(--green);color:var(--white);font-size:8px;font-weight:800;display:flex;align-items:center;justify-content:center}

/* teaser band */
.teasers{left:0;top:280px;width:750px;height:288px;background:var(--green-pale);border-top:3px solid var(--green);border-bottom:2px solid var(--green)}
.teasers h1{position:absolute;left:0;width:750px;top:31px;text-align:center;font-size:16.5px;font-weight:400;color:var(--green)}
.teasers p{position:absolute;left:50px;width:650px;top:57px;text-align:center;font-size:7px;line-height:12px;color:var(--grey)}
.dots{border-top:1px dotted var(--green)}
.teaser-img{width:112px;height:112px;border-radius:50%;border:4px solid var(--green);background:linear-gradient(135deg,#e9eef2,#9aa4ad 60%,#4b5560)}
.teaser-cap{width:160px;text-align:center;font-size:8.5px;line-height:12px;color:var(--grey);letter-spacing:.2px}

/* content */
.content h2{left:101px;top:603px;font-size:16px;font-weight:400;color:var(--green);letter-spacing:.3px}
.body-text{left:101px;width:292px;font-size:7.2px;line-height:12px;color:var(--text)}
.sub-head{left:94px;font-size:7.5px;color:var(--green)}
.blog-title{left:467px;top:602px;font-size:10px;font-weight:600;color:var(--green);letter-spacing:.5px}
.blog-img{width:34px;height:34px;border-radius:50%;background:linear-gradient(135deg,#dfe4e8,#8d98a2)}
.blog-text{left:516px;width:135px;font-size:6px;line-height:12px;color:var(--text)}
.blog-text .more{color:var(--green)}
.news-title{left:463px;top:831px;font-size:11px;font-weight:600;color:var(--green);letter-spacing:.5px}
.news-input{left:461px;top:852px;width:190px;height:20px;border-radius:10px;background:#e6e6e6;font-size:6px;color:var(--grey);padding-left:10px;display:flex;align-items:center}

/* partners */
.partners{left:130px;top:927px;width:492px;height:96px;border-radius:48px;background:var(--green)}
.badge{background:#1f5fae}

/* footer */
.foot-links{left:100px;top:1055px;font-size:8px;line-height:15px;color:var(--light)}
.foot-head{font-size:7.5px;color:var(--green)}
.foot-small{font-size:6px;line-height:12px;color:#b9b9b9}
.follow{left:570px;top:1056px;font-size:8.5px;color:var(--light);letter-spacing:.3px}
.social{width:21px;height:21px;border-radius:50%;background:var(--green);top:1071px}
.copy{left:0;width:750px;top:1153px;text-align:center;font-size:7.5px;line-height:12px;color:#b9b9b9}
</style>
</head>
<body>

<header class="site-header abs">
  <div class="brand abs"><span class="brand-name">TAVI</span><span class="brand-tag">Training • Coaching • Consulting</span></div>
  <nav class="main-nav abs">
    <span class="item active">HOME</span><span class="sep">I</span>
    <span class="item">ÜBER UNS<span class="caret">&#8964;</span></span><span class="sep">I</span>
    <span class="item">FÜR TRAINERS<span class="caret">&#8964;</span></span><span class="sep">I</span>
    <span class="item">REFERENZEN</span><span class="sep">I</span>
    <span class="item">KONTAKT</span>
  </nav>
</header>

<section class="hero abs" role="img" aria-label="Nahaufnahme eines sich entrollenden grünen Farnwedels">
</section>
<svg class="hero-arrow abs" style="left:15px" width="28" height="44" viewBox="0 0 28 44"><polyline points="22,4 6,22 22,40" fill="none" stroke="#a2c61b" stroke-width="7" stroke-linecap="round" stroke-linejoin="round"/></svg>
<svg class="hero-arrow abs" style="left:700px" width="28" height="44" viewBox="0 0 28 44"><polyline points="6,4 22,22 6,40" fill="none" stroke="#a2c61b" stroke-width="7" stroke-linecap="round" stroke-linejoin="round"/></svg>
<div class="hero-title abs"><span class="chev">&#8250;</span>TRAINING, COACHING<br>CONSULTING <b>FÜR TRAINER</b></div>
<div class="hero-sub abs">Lorem ipsum dolor sit amet consectetur adipiscing elit.<br>Aliquam vehicula, mauris non</div>
<div class="btn abs">MEHR ERFAHREN</div>

<section class="teasers abs">
  <h1>LOREM IPSUM DOLOR SIT AMET CONSECTETUR ADIPISCING ELIT.</h1>
  <p>Lorem ipsum dolor sit amet, consectetur adipiscing elit. Aliquam vehicula, mauris non eleifend vehicula, lorem turpis fringilla nisi, at feugiat dolor sapien sit amet mauris. In quam dolor, fringilla eget lacinia et, dignissim et purus. Maecenas euismod vel elit nec gravida. Pellentesque pretium ornare lobortis. Aliquam at pulvinar mi. Nulla eget bibendum nisl. Integer consectetur quam ac purus pharetra pulvinar. Aenean faucibus tortor ac tortor aliquet tincidunt. Mauris eget maximus urna.</p>
  <div class="dots abs" style="left:68px;top:99px;width:625px"></div>
  <div class="teaser-img abs" style="left:143px;top:117px" role="img" aria-label="Gefaltete Hände auf einem Schreibtisch"></div>
  <div class="teaser-img abs" style="left:318px;top:117px" role="img" aria-label="Zwei Personen im Gespräch über Unterlagen"></div>
  <div class="teaser-img abs" style="left:493px;top:117px" role="img" aria-label="Hände mit Tablet bei einer Besprechung"></div>
  <div class="teaser-cap abs" style="left:119px;top:241px">LOREM IPSUM DOLOR SIT<br>AMET MAURIS VOT KALEM</div>
  <div class="teaser-cap abs" style="left:294px;top:241px">CONSECTETUR ADIPISCING<br>ELIT NON VEHICULA</div>
  <div class="teaser-cap abs" style="left:469px;top:241px">DOLOR SIT AMET<br>CONSECTETUR LOREM ELIT</div>
</section>

<main class="content">
  <h2 class="abs">LOREM IPSUM DOLOR</h2>
  <div class="dots abs" style="left:101px;top:630px;width:281px"></div>
  <p class="body-text abs" style="top:640px">Vestibulum nec mauris facilisis, suscipit est et, sagittis erat. Duis eget ante rutrum, congue sapien non, accumsan ante. Phasellus vehicula gravida semper. Nulla sapien nisl, mollis in feugiat ac, bibendum vel justo. Morbi et tincidunt erat. Quisque in vestibulum enim. Maecenas imperdiet accumsan libero non gravida. Curabitur et tristique diam, nec sagittis nibh. Nullam vehicula sem eget lectus aliquet, at finibus orci sagittis. Duis sagittis lobortis turpis, et fermentum turpis feugiat at. Vivamus mi felis, convallis non ante venenatis, ornare mattis magna. Ut a tincidunt diam.</p>
  <div class="sub-head abs" style="top:747px">&#8250; Vestibulum nec mauris facilisis,</div>
  <p class="body-text abs" style="top:759px">suscipit est et, sagittis erat. Duis eget ante rutrum, congue sapien non, accumsan ante. Phasellus vehicula gravida semper. Nulla sapien nisl, mollis in feugiat ac, bibendum vel justo. Morbi et tincidunt erat. Quisque in vestibulum enim. Maecenas imperdiet accumsan libero non gravida.</p>
  <div class="sub-head abs" style="top:819px">&#8250; Curabitur et tristique diam, nec sagittis nibh.</div>
  <p class="body-text abs" style="top:831px">Nullam vehicula sem eget lectus aliquet, at finibus orci sagittis. Duis sagittis lobortis turpis, et fermentum turpis feugiat at. Vivamus mi felis, convallis non ante venenatis, ornare mattis magna. Ut a tincidunt diam. Curabitur commodo ex ut est feugiat, eu sodales massa accumsan.</p>

  <div class="blog-title abs">BLOG</div>
  <div class="blog-img abs" style="left:466px;top:636px" role="img" aria-label="Blogbild: Geschäftsleute im Gespräch"></div>
  <p class="blog-text abs" style="top:632px">Lorem ipsum dolor sit amet, consectetur adipiscing elit. In dapibus accumsan luctus. Aliquam posuere eros sed nibh sagittis,<br><span class="more">more &nbsp;&#8250;</span></p>
  <div class="dots abs" style="left:465px;top:686px;width:186px"></div>
  <div class="blog-img abs" style="left:466px;top:698px" role="img" aria-label="Blogbild: Trainer am Arbeitsplatz"></div>
  <p class="blog-text abs" style="top:696px">Pellentesque habitant morbi tristique senec-tus et netus et malesuada fames ac turpis egestas.<br><span class="more">more &nbsp;&#8250;</span></p>
  <div class="dots abs" style="left:465px;top:750px;width:186px"></div>
  <div class="blog-img abs" style="left:466px;top:762px" role="img" aria-label="Blogbild: Besprechung mit Tablet"></div>
  <p class="blog-text abs" style="top:760px">Mauris sollicitudin felis aliquam ipsum dictum vehicula. Donec feugiat sapien nunc, quis auctor libero finibus in.<br><span class="more">more &nbsp;&#8250;</span></p>
  <div class="dots abs" style="left:465px;top:814px;width:186px"></div>

  <div class="news-title abs">NEWSLETTER ABONNIEREN</div>
  <div class="news-input abs">enter your email id here ...</div>
</main>

<svg class="abs" style="left:0;top:880px" width="750" height="320" viewBox="0 0 750 320">
  <path d="M0,30 Q375,150 750,25 L750,320 L0,320 Z" fill="#d9d9d9"/>
  <path d="M0,58 Q375,170 750,60 L750,320 L0,320 Z" fill="#232528"/>
</svg>

<section class="partners abs">
  <div class="badge abs" style="left:63px;top:23px;width:36px;height:45px" role="img" aria-label="Verbandsabzeichen Mitglied"></div>
  <div class="abs" style="left:103px;top:58px;width:7px;height:7px;background:#333"></div>
  <div class="badge abs" style="left:192px;top:24px;width:38px;height:45px" role="img" aria-label="Verbandsabzeichen"></div>
  <div class="abs" style="left:236px;top:36px;width:60px;height:20px;border-radius:3px;background:#8aa816"></div>
  <div class="badge abs" style="left:338px;top:37px;width:98px;height:23px" role="img" aria-label="Zertifikat geprüfter Business-Trainer"></div>
</section>

<footer>
  <div class="foot-links abs">HOME<br>ÜBER UNS<br>FÜR TRAINERS<br>REFERENZEN<br>KONTAKT</div>

  <svg class="abs" style="left:192px;top:1054px" width="14" height="12" viewBox="0 0 14 12"><path d="M7,0 L14,6 L12,6 L12,12 L8.5,12 L8.5,8 L5.5,8 L5.5,12 L2,12 L2,6 L0,6 Z" fill="#a2c61b"/></svg>
  <div class="abs" style="left:217px;top:1055px"><div class="foot-head">Address</div><div class="foot-small" style="color:#e0e0e0">Vestibulum nec mauris 62<br>Suscipit est et<br>62134 Townname</div></div>

  <svg class="abs" style="left:316px;top:1054px" width="12" height="12" viewBox="0 0 12 12"><rect width="12" height="12" rx="2" fill="#a2c61b"/><path d="M3.5,3 Q3,7 8.5,9 L9.3,7.8 L7.8,6.8 L7,7.5 Q5.3,6.7 4.7,5 L5.4,4.3 L4.5,2.7 Z" fill="#232528"/></svg>
  <div class="abs" style="left:341px;top:1055px"><div class="foot-head">Phone</div><div class="foot-small">(000 &nbsp;123 &nbsp;7658 903<br>(000 &nbsp;123 &nbsp;7658 903<br>(000 &nbsp;123 &nbsp;7658 903</div></div>

  <svg class="abs" style="left:429px;top:1055px" width="13" height="9" viewBox="0 0 13 9"><rect width="13" height="9" fill="#a2c61b"/><polyline points="0,0 6.5,5 13,0" fill="none" stroke="#232528" stroke-width="1"/></svg>
  <div class="abs" style="left:454px;top:1055px"><div class="foot-head">Email</div><div class="foot-small">info@tavi.com<br>addressinfo@tavi.com<br>emailadd@tavi.com</div></div>

  <div class="follow abs">BITTE FOLGEN</div>
  <div class="social abs" style="left:563px" role="img" aria-label="Pinnwald"></div>
  <div class="social abs" style="left:590px" role="img" aria-label="Zwitscherhof"></div>
  <div class="social abs" style="left:616px" role="img" aria-label="Kontaktor"></div>

  <div class="abs" style="left:188px;top:1150px;width:382px;border-top:1px dotted #9a9a9a"></div>
  <p class="copy abs">Aliquam at pulvinar mi. Nulla eget bibendum nisl. Integer consectetur quam ac purus pharetra pulvinar.<br>Aenean faucibus tortor ac tortor aliquet tincidunt. Mauris eget maximus urna.</p>
</footer>

</body>
</html>
```